Valdane Companies Business Card Design

We need a new business card for our Private Equity Real Estate Development firm, “Valdane” and our EB-5 regional center “Thornmere Regional Center” on one card. We prefer a design that is simple, elegant, and represents the luxury products we design and build as well as the financial security and stability our successful history has produced. We are an industry leader in our field and 3rd generation family business that has evolved into an institutional quality investment platform. Considered design size is standard business card dimensions (3.5 x 2 inches with an additional 1/8 inch space for design elements or backgrounds that extend beyond the finished size of your piece.

Target Market(s)

• High net worth individuals
• Highly skilled technical workers and physicians in the US seeking investment-based immigration opportunities
• Sophisticated private equity investors
• Intermediary partners include domestic attorneys and investment brokers, as well as international agent networks
• US real estate developers

Industry/Entity Type

Finance

Contact Information for Business Card

(Providing placeholder info for personal information, please design for longer character spaces, longer names and addresses etc..)
• Logo for Valdane
• Logo for Thornmere Regional Center
• Full name: Marcus Valdane
• Job title: CEO
• Email address: mvaldane@valdanecompanies.com
• Cell phone number: +1.555.314.2287
• Office number +1.555.628.4410
• Office address: Larkfield Court 5, 4817 Vista Orilla, San Ramon, CA.
• Website: www.valdanecompanies.com

Font styles to use
Serif
Sans Serif

Colors
ec1f27
ffffff
000000

Requirements
Must have
• • Logo for Valdane
• • Logo for Thornmere Regional Center
• - Use rounded corners
• (See .ai file included for logos)
Nice to have
• • Simple, elegant design
• • Aesthetically compatible with our website design (www.valdanecompanies.com)
• • Color palette including but not limited to white, black, and red (as per logos)
Should not have
• - Not too much red color
• - Do not stack both logos on top of each other

```html
<!DOCTYPE html>
<html lang="en">
<head>
<meta charset="utf-8">
<title>Valdane Companies Business Card</title>
<link href="https://fonts.googleapis.com/css2?family=Cinzel:wght@400;600;700&family=Open+Sans:wght@400;600&display=swap" rel="stylesheet">
<style>
  :root {
    --backdrop: #8a8a8a;
    --paper: #efefef;
    --charcoal: #2c2c2c;
    --charcoal-soft: #323232;
    --ink: #262626;
    --accent-red: #a31b2e;
    --light-text: #f2f2f2;
    --muted-text: #c9c9c9;
    --rule: #6a6a6a;
  }
  * { margin: 0; padding: 0; box-sizing: border-box; }
  html, body { width: 1200px; height: 1200px; overflow: hidden; }
  body {
    background: var(--backdrop);
    position: relative;
    font-family: "Open Sans", Arial, sans-serif;
  }
  .card {
    position: absolute;
    top: 310px;
    width: 365px;
    height: 595px;
    overflow: hidden;
    border-radius: 4px;
  }
  .card--front { left: 234px; background: var(--paper); }
  .card--back { left: 628px; width: 368px; background: var(--charcoal); }

  .front-shapes { position: absolute; inset: 0; }

  .brand-mark-square {
    position: absolute;
    left: 152px; top: 52px;
    width: 60px; height: 60px;
    background: var(--ink);
  }
  .brand-name {
    position: absolute;
    left: 0; right: 0; top: 150px;
    text-align: center;
    font-family: "Cinzel", "Times New Roman", serif;
    font-weight: 700;
    color: var(--ink);
  }
  .brand-name__main { display: block; font-size: 48px; line-height: 1; letter-spacing: 1px; }
  .brand-name__sub { display: block; font-size: 15px; letter-spacing: 7px; margin-top: 10px; }

  .holder {
    position: absolute;
    left: 0; right: 0; top: 344px;
    text-align: center;
    color: var(--light-text);
  }
  .holder__name {
    font-family: "Cinzel", "Times New Roman", serif;
    font-size: 24px;
    font-weight: 600;
    letter-spacing: 0.5px;
    line-height: 30px;
  }
  .holder__title { font-size: 15px; line-height: 22px; margin-top: 2px; }
  .divider {
    width: 228px; height: 1px;
    background: var(--rule);
    margin: 8px auto 10px;
  }
  .contact-list { list-style: none; font-size: 15.5px; line-height: 21.5px; }
  .contact-list b { font-weight: 600; }
  .address { font-size: 15.5px; line-height: 21.5px; }

  .pattern-field {
    position: absolute; inset: 0;
    background: linear-gradient(180deg, var(--charcoal-soft), var(--charcoal));
  }
  .center-lockup {
    position: absolute;
    left: 34px; top: 486px;
    display: flex;
    align-items: center;
    gap: 22px;
  }
  .center-lockup__square {
    width: 52px; height: 52px;
    background: var(--muted-text);
  }
  .center-lockup__name {
    font-family: "Cinzel", "Times New Roman", serif;
    font-weight: 400;
    color: var(--muted-text);
  }
  .center-lockup__main { display: block; font-size: 33px; line-height: 1; }
  .center-lockup__sub { display: block; font-size: 11px; letter-spacing: 4.5px; margin-top: 6px; }
</style>
</head>
<body>

<section class="card card--front" aria-label="Card front">
  <svg class="front-shapes" width="365" height="595" viewBox="0 0 365 595" aria-hidden="true">
    <polygon points="0,297 350,251 365,250 365,253 0,330" fill="var(--accent-red)"/>
    <polygon points="0,330 365,253 365,595 0,595" fill="var(--charcoal)"/>
  </svg>

  <div class="brand-mark-square"></div>
  <h1 class="brand-name">
    <span class="brand-name__main">VALDANE</span>
    <span class="brand-name__sub">CAPITAL</span>
  </h1>

  <div class="holder">
    <p class="holder__name">MARCUS VALDANE</p>
    <p class="holder__title">CEO</p>
    <div class="divider"></div>
    <ul class="contact-list">
      <li><b>P:</b> +1.555.314.2287</li>
      <li><b>M:</b> +1.555.628.4410</li>
      <li><b>E:</b> mvaldane@valdanecompanies.com</li>
      <li><b>W:</b> www.valdanecompanies.com</li>
    </ul>
    <div class="divider"></div>
    <p class="address">Larkfield Court 5, 4817 Vista<br>Orilla, San Ramon, CA</p>
  </div>
</section>

<section class="card card--back" aria-label="Card back">
  <div class="pattern-field" role="img" aria-label="Faint repeating brand pattern across the dark card back"></div>
  <div class="center-lockup">
    <div class="center-lockup__square"></div>
    <p class="center-lockup__name">
      <span class="center-lockup__main">THORNMERE</span>
      <span class="center-lockup__sub">REGIONAL CENTER</span>
    </p>
  </div>
</section>

</body>
</html>
```